AI Business Tools Landing Page

My web-based website builder (Pavlora.com) will be adding many new features in the very near future and I need an eye-catching landing page to promote these new products.

The page will have a primary section of the 8 main products we are promoting:
1. AI Instant Website Generator
2. AI Chatbot
3. Online Store Builder with AI Assistance
4. AI Auto-Blogging System
5. Online Scheduling System
6. Custom Email System
7. SEO Service
8. CRM System

The page will also have a smaller section for links to our affiliate programs. These can be smaller, less-promanent buttons or links. These are the affiliate products:
1. Get Your LLC
2. Website Design and Maintenance
3. Kestrova Ads Management
4. Social Media Posting Service
5. Logo Design
6. Trademark Registration
7. Patent Application
8. Printing Services (including postcards, flyers, and merch.)
9. Bulk AI Content Generator

The theme and color scheme of the page should follow the theme of our main website, which is https://pavlora.com.

I need the page fully coded and ready to deploy on my server.

I look forward to seeing your amazing designs!

```html
<!DOCTYPE html>
<html lang="en">
<head>
<meta charset="utf-8">
<title>Pavlora – Additional Features &amp; Tools for Website</title>
<link href="https://fonts.googleapis.com/css2?family=Poppins:wght@400;500;600;700;800&family=Lexend:wght@300;400;500&display=swap" rel="stylesheet">
<style>
:root{
  --navy:#0b1c3a;
  --navy-deep:#07132b;
  --blue:#1fa3e8;
  --blue-bright:#29b6f6;
  --blue-soft:#dff1fc;
  --line:#b9d9ee;
  --ink:#0d1a33;
  --text:#1c2740;
  --muted:#6b7489;
  --panel:#f2f8fd;
  --white:#ffffff;
}
*{box-sizing:border-box;margin:0;padding:0}
html,body{width:1200px;height:2502px;overflow:hidden}
body{position:relative;background:var(--white);font-family:"Lexend",sans-serif;color:var(--text)}
a{text-decoration:none}

/* hero */
.hero{position:absolute;left:0;top:0;width:1200px;height:680px;background:linear-gradient(120deg,var(--navy-deep) 0%,#0d2650 45%,#14508a 100%);overflow:hidden}
.hero-art{position:absolute;right:0;top:60px;width:760px;height:520px;background:radial-gradient(ellipse at 55% 45%,rgba(255,170,110,.55) 0%,rgba(80,160,230,.35) 30%,rgba(20,60,120,0) 70%)}
.brand{position:absolute;display:flex;align-items:center;gap:10px;color:var(--white);font-family:"Poppins",sans-serif;font-weight:600;text-decoration:none}
.brand-mark{width:34px;height:34px;border-radius:8px;background:var(--blue-bright)}
.hero .brand{left:130px;top:32px;font-size:32px}
.hero-title{position:absolute;left:126px;top:262px;color:var(--white);font-family:"Poppins",sans-serif;line-height:1.18}
.hero-title strong{display:block;font-size:46px;font-weight:700}
.hero-title span{display:block;font-size:46px;font-weight:400}
.hero-wave{position:absolute;left:0;bottom:0;width:1200px;height:110px}
.hero-connector{position:absolute;left:590px;top:575px;width:2px;height:90px;background:var(--blue)}
.hero-connector::after{content:"";position:absolute;left:-4px;bottom:-6px;width:10px;height:10px;border-radius:50%;background:var(--blue)}

/* features */
.section-title{position:absolute;left:0;width:1200px;text-align:center;font-family:"Poppins",sans-serif;font-size:33px;font-weight:400;color:var(--ink)}
.section-title b{font-weight:800}
.features-title{top:706px}
.features-title::after{content:"";display:block;width:76px;height:3px;background:var(--blue);margin:8px auto 0}
.features{position:absolute;left:82px;top:806px;width:1034px;display:grid;grid-template-columns:517px 517px}
.feature{display:flex;align-items:center;gap:24px;height:242px;padding:0 18px 0 22px;border-bottom:1px solid var(--line)}
.feature:nth-child(odd){border-right:1px solid var(--line)}
.feature:nth-child(7),.feature:nth-child(8){border-bottom:none}
.feature-art{flex:0 0 180px;height:180px;border-radius:50%;background:radial-gradient(circle at 45% 40%,#e9f6fe 0%,#9fd6f6 55%,#2a9ae0 100%)}
.feature-art.deep{background:radial-gradient(circle at 45% 40%,#3a7fd6 0%,#1a3d8e 60%,#0f2762 100%)}
.feature-art.pale{background:radial-gradient(circle at 50% 50%,#f4fafe 0%,#d6ecfb 70%,#b8def7 100%)}
.feature-body h3{font-family:"Poppins",sans-serif;font-size:18px;font-weight:600;color:var(--ink);line-height:1.2;margin-bottom:12px}
.feature-body ul{list-style:none}
.feature-body li{position:relative;padding-left:26px;font-size:11.2px;line-height:1.18;color:var(--text);margin-bottom:20px}
.feature-body li:last-child{margin-bottom:0}
.tick{position:absolute;left:0;top:50%;margin-top:-9px;width:18px;height:18px}

/* tools */
.tools{position:absolute;left:0;top:1832px;width:1200px;height:470px;background:var(--panel)}
.tools-title{top:1878px}
.tool-grid{position:absolute;left:99px;top:1969px;width:1021px;display:grid;grid-template-columns:333px 333px 333px;column-gap:11px;row-gap:16px}
.tool{display:flex;align-items:center;gap:10px;height:64px;padding:0 10px 0 34px;border:2px solid #a9d4f2;border-radius:4px;background:var(--white);font-family:"Poppins",sans-serif;font-size:14.5px;font-weight:500;color:var(--ink);white-space:nowrap}
.tool svg{flex:0 0 36px;width:36px;height:36px}
.tool small{display:block;font-family:"Lexend",sans-serif;font-size:10.5px;font-weight:300;color:var(--muted)}
.tool.active{background:var(--navy);border-color:var(--navy);color:var(--white)}
.tool.link{color:var(--blue)}

/* footer */
.footer{position:absolute;left:0;top:2270px;width:1200px;height:232px;background:var(--navy)}
.footer-wave{position:absolute;left:0;top:0;width:1200px;height:80px}
.footer .brand{left:110px;top:104px;font-size:32px}
.copyright{position:absolute;left:0;width:1200px;top:128px;text-align:center;color:#d7e2f2;font-size:15px}
.social{position:absolute;left:903px;top:114px;width:190px;display:grid;grid-template-columns:repeat(5,22px);column-gap:15px;row-gap:14px}
.social span{width:22px;height:22px;border-radius:50%;background:var(--white)}
</style>
</head>
<body>

<header class="hero">
  <div class="hero-art" role="img" aria-label="Robotic hand and human hand reaching toward a glowing emblem among digital network lines"></div>
  <a class="brand" href="https://pavlora.com"><span class="brand-mark"></span>Pavlora</a>
  <h1 class="hero-title"><strong>Additional Features</strong><span>&amp; Tools for Website</span></h1>
  <svg class="hero-wave" viewBox="0 0 1200 110" preserveAspectRatio="none" aria-hidden="true">
    <path d="M0 62 C260 -10 520 40 760 70 C960 95 1100 80 1200 58 L1200 110 L0 110 Z" fill="var(--blue-bright)"/>
    <path d="M0 84 C260 20 520 50 760 82 C960 108 1100 96 1200 78 L1200 110 L0 110 Z" fill="#ffffff"/>
  </svg>
</header>
<div class="hero-connector"></div>

<h2 class="section-title features-title">Additional Features <b>for Your Website</b></h2>

<main class="features">
  <article class="feature">
    <div class="feature-art pale" role="img" aria-label="Hand tapping a website template on a screen"></div>
    <div class="feature-body">
      <h3>AI Instant Website<br>Generator</h3>
      <ul>
        <li><svg class="tick" viewBox="0 0 18 18"><circle cx="9" cy="9" r="9" fill="var(--blue-soft)"/><path d="M5 9.2l2.6 2.6L13 6.4" fill="none" stroke="var(--blue)" stroke-width="1.8"/></svg>Get a professional, SEO-optimized website in seconds!</li>
        <li><svg class="tick" viewBox="0 0 18 18"><circle cx="9" cy="9" r="9" fill="var(--blue-soft)"/><path d="M5 9.2l2.6 2.6L13 6.4" fill="none" stroke="var(--blue)" stroke-width="1.8"/></svg>Includes custom domain, secure high-speed hosting, professional images, and more!</li>
      </ul>
    </div>
  </article>
  <article class="feature">
    <div class="feature-art" role="img" aria-label="Chatbot robot above a glowing tablet"></div>
    <div class="feature-body">
      <h3>AI ChatBot</h3>
      <ul>
        <li><svg class="tick" viewBox="0 0 18 18"><circle cx="9" cy="9" r="9" fill="var(--blue-soft)"/><path d="M5 9.2l2.6 2.6L13 6.4" fill="none" stroke="var(--blue)" stroke-width="1.8"/></svg>Fully-trainable ChatBot will learn about your business to automate the customer support process!</li>
        <li><svg class="tick" viewBox="0 0 18 18"><circle cx="9" cy="9" r="9" fill="var(--blue-soft)"/><path d="M5 9.2l2.6 2.6L13 6.4" fill="none" stroke="var(--blue)" stroke-width="1.8"/></svg>Built-in CRM features integrate emailing, text messaging, and contact forms!</li>
      </ul>
    </div>
  </article>
  <article class="feature">
    <div class="feature-art pale" role="img" aria-label="Isometric online storefront with laptop and payment cards"></div>
    <div class="feature-body">
      <h3>Online Store Builder<br>(E-Commerce) with<br>AI Assistance</h3>
      <ul>
        <li><svg class="tick" viewBox="0 0 18 18"><circle cx="9" cy="9" r="9" fill="var(--blue-soft)"/><path d="M5 9.2l2.6 2.6L13 6.4" fill="none" stroke="var(--blue)" stroke-width="1.8"/></svg>Sell you products online and integrate your products into any website!</li>
        <li><svg class="tick" viewBox="0 0 18 18"><circle cx="9" cy="9" r="9" fill="var(--blue-soft)"/><path d="M5 9.2l2.6 2.6L13 6.4" fill="none" stroke="var(--blue)" stroke-width="1.8"/></svg>Accept payments from multiple payment gateways including Quopaxa and Velmintra!</li>
      </ul>
    </div>
  </article>
  <article class="feature">
    <div class="feature-art pale" role="img" aria-label="Blogging dashboard windows with article previews"></div>
    <div class="feature-body">
      <h3>AI Auto-Blogging System</h3>
      <ul>
        <li><svg class="tick" viewBox="0 0 18 18"><circle cx="9" cy="9" r="9" fill="var(--blue-soft)"/><path d="M5 9.2l2.6 2.6L13 6.4" fill="none" stroke="var(--blue)" stroke-width="1.8"/></svg>AI will generate an incredible blog for your business in seconds and immediately begin posting content for you!</li>
        <li><svg class="tick" viewBox="0 0 18 18"><circle cx="9" cy="9" r="9" fill="var(--blue-soft)"/><path d="M5 9.2l2.6 2.6L13 6.4" fill="none" stroke="var(--blue)" stroke-width="1.8"/></svg>Choose from daily, weekly, or monthly automated blog posting. Consistent, unique, SEO-optimized content posting on cruise control!</li>
      </ul>
    </div>
  </article>
  <article class="feature">
    <div class="feature-art" role="img" aria-label="Tablet showing a monthly appointment calendar"></div>
    <div class="feature-body">
      <h3>Online Scheduling System</h3>
      <ul>
        <li><svg class="tick" viewBox="0 0 18 18"><circle cx="9" cy="9" r="9" fill="var(--blue-soft)"/><path d="M5 9.2l2.6 2.6L13 6.4" fill="none" stroke="var(--blue)" stroke-width="1.8"/></svg>Get appointment bookings, restaurant reservations, or consultations scheduled directly from your website!</li>
        <li><svg class="tick" viewBox="0 0 18 18"><circle cx="9" cy="9" r="9" fill="var(--blue-soft)"/><path d="M5 9.2l2.6 2.6L13 6.4" fill="none" stroke="var(--blue)" stroke-width="1.8"/></svg>Manage your employees' schedules and all your appointments from a simple, user-friendly dashboard!</li>
      </ul>
    </div>
  </article>
  <article class="feature">
    <div class="feature-art pale" role="img" aria-label="Email inbox windows with a custom domain address"></div>
    <div class="feature-body">
      <h3>Custom emails using<br>your domain</h3>
      <ul>
        <li><svg class="tick" viewBox="0 0 18 18"><circle cx="9" cy="9" r="9" fill="var(--blue-soft)"/><path d="M5 9.2l2.6 2.6L13 6.4" fill="none" stroke="var(--blue)" stroke-width="1.8"/></svg>Quickly set up emails for yourself and all your employees with your own domain extension (example – johnd@yoursite.com). No more unprofessional Mailquorra and Trevinmail email addresses!</li>
        <li><svg class="tick" viewBox="0 0 18 18"><circle cx="9" cy="9" r="9" fill="var(--blue-soft)"/><path d="M5 9.2l2.6 2.6L13 6.4" fill="none" stroke="var(--blue)" stroke-width="1.8"/></svg>Manage all your business emails from a simple, user-friendly interface!</li>
      </ul>
    </div>
  </article>
  <article class="feature">
    <div class="feature-art pale" role="img" aria-label="Laptop with backlink building diagram and linked pages"></div>
    <div class="feature-body">
      <h3>SEO Service – Automatic<br>Backlink Building</h3>
      <ul>
        <li><svg class="tick" viewBox="0 0 18 18"><circle cx="9" cy="9" r="9" fill="var(--blue-soft)"/><path d="M5 9.2l2.6 2.6L13 6.4" fill="none" stroke="var(--blue)" stroke-width="1.8"/></svg>Let us do the hard work of getting high-quality backlinks to your website. Although difficult to get, backlinks to your website boost search engine ranking more than any other strategy!</li>
        <li><svg class="tick" viewBox="0 0 18 18"><circle cx="9" cy="9" r="9" fill="var(--blue-soft)"/><path d="M5 9.2l2.6 2.6L13 6.4" fill="none" stroke="var(--blue)" stroke-width="1.8"/></svg>Subscribe now and start getting 10-20 high-quality permanent backlinks to your website every month, guaranteed!</li>
      </ul>
    </div>
  </article>
  <article class="feature">
    <div class="feature-art deep" role="img" aria-label="Isometric CRM dashboard with charts, gears and coins"></div>
    <div class="feature-body">
      <h3>Customer Relationship<br>Management (CRM) System</h3>
      <ul>
        <li><svg class="tick" viewBox="0 0 18 18"><circle cx="9" cy="9" r="9" fill="var(--blue-soft)"/><path d="M5 9.2l2.6 2.6L13 6.4" fill="none" stroke="var(--blue)" stroke-width="1.8"/></svg>Automate the lead follow up process to consistently stay in front of your potential customers!</li>
        <li><svg class="tick" viewBox="0 0 18 18"><circle cx="9" cy="9" r="9" fill="var(--blue-soft)"/><path d="M5 9.2l2.6 2.6L13 6.4" fill="none" stroke="var(--blue)" stroke-width="1.8"/></svg>Schedule automatic email and text campaigns and effortlessly follow your funnels from lead to closing!</li>
      </ul>
    </div>
  </article>
</main>

<section class="tools" aria-label="More tools"></section>
<h2 class="section-title tools-title">More Tools to Help You <b>Grow Your Business</b></h2>
<nav class="tool-grid">
  <a class="tool" href="#"><svg viewBox="0 0 36 36" fill="none" stroke="var(--blue)" stroke-width="1.6"><rect x="4" y="11" width="28" height="19" rx="2"/><path d="M13 11V7h10v4M4 19h28"/></svg>Get Your LLC</a>
  <a class="tool active" href="#"><svg viewBox="0 0 36 36" fill="none" stroke="#ffffff" stroke-width="1.6"><rect x="3" y="7" width="24" height="11" rx="5.5"/><path d="M18 16l3 14 3-5 5 3 1-2-5-3 4-3z"/></svg>Social Media Posting Service</a>
  <a class="tool" href="#"><svg viewBox="0 0 36 36" fill="none" stroke="var(--blue)" stroke-width="1.6"><rect x="4" y="6" width="28" height="20" rx="2"/><path d="M18 26v5M11 31h14M9 12h10M9 17h14"/></svg>Patent Application</a>
  <a class="tool" href="#"><svg viewBox="0 0 36 36" fill="none" stroke="var(--blue)" stroke-width="1.6"><rect x="3" y="5" width="26" height="22" rx="2"/><path d="M3 11h26M11 17l-3 3 3 3M17 17l3 3-3 3"/><circle cx="27" cy="27" r="5"/></svg>Website Design and Maintenance</a>
  <a class="tool link" href="#"><svg viewBox="0 0 36 36" fill="none" stroke="var(--blue)" stroke-width="1.6"><rect x="5" y="5" width="26" height="26"/><path d="M11 27l7-18 7 18M14 21h8"/></svg>Logo Design</a>
  <a class="tool" href="#"><svg viewBox="0 0 36 36" fill="none" stroke="var(--blue)" stroke-width="1.6"><rect x="10" y="4" width="16" height="9"/><rect x="4" y="13" width="28" height="12" rx="2"/><rect x="10" y="21" width="16" height="11"/></svg><span>Printing Services<small>(including postcards, flyers, and merch.)</small></span></a>
  <a class="tool" href="#"><svg viewBox="0 0 36 36" fill="none" stroke="var(--blue)" stroke-width="1.6"><path d="M5 29L15 8l4 7M19 15l9 14H5"/></svg>Kestrova Ads Management</a>
  <a class="tool link" href="#"><svg viewBox="0 0 36 36" fill="none" stroke="var(--blue)" stroke-width="1.6"><circle cx="18" cy="18" r="14"/><circle cx="18" cy="18" r="10"/><path d="M11 15h6M14 15v8M19 23v-8l2.5 4 2.5-4v8"/></svg>Trademark Registration</a>
  <a class="tool" href="#"><svg viewBox="0 0 36 36" fill="none" stroke="var(--blue)" stroke-width="1.6"><rect x="4" y="6" width="20" height="26" rx="1"/><path d="M8 12h12M8 17h12M8 22h8M30 10L18 28l-1 4 4-2 12-18z"/></svg>Bulk AI Content Generator</a>
</nav>

<footer class="footer">
  <svg class="footer-wave" viewBox="0 0 1200 80" preserveAspectRatio="none" aria-hidden="true">
    <path d="M0 0 L1200 0 L1200 8 C1000 60 700 60 420 40 C250 28 100 40 0 60 Z" fill="var(--panel)"/>
    <path d="M0 60 C100 40 250 28 420 40 C700 60 1000 60 1200 8 L1200 22 C1000 80 700 80 420 56 C250 42 100 50 0 70 Z" fill="var(--blue-bright)"/>
  </svg>
  <a class="brand" href="https://pavlora.com"><span class="brand-mark"></span>Pavlora</a>
  <p class="copyright">© 2024 Pavlora. All Rights Reserved</p>
  <div class="social" aria-label="Social links">
    <span></span><span></span><span></span><span></span><span></span>
    <span></span><span></span><span></span><span></span><span></span>
  </div>
</footer>

</body>
</html>
```